New patented product needs a snazzy brochure

We are an equipment manufacturing company located in Sydney Australia. We require an A5 size 4 page brochure designed to promote a new product we are just about to launch.

Our new machine is called a sheet following system and is used in conjunction with brake presses (machines used to fold sheet and plate metal). It basically supports large sheets of metal in the folding process to save the arms and backs of operators.

You can see from the attached photos the actual machine is painted red and black. We would like some of that colour incorporated in the design of the brochure.

The machine is patented, as we are unique to other systems on the market. We can retrofit to any existing machine as well as be used with other brake presses in their factory. Our competitors' units can only be used on the break press machine they are installed on. If you have a second hand break press, we are your only option.

Two or more of the units are used in conjunction with a press brake, depending on it's length and the length of the material being folded.
Updates

I have now guaranteed this project.  More photos have been added as well as logo.  Text is being worked on now and will be uploaded very shortly.

Reason: Hi Guys I have extended the deadline as I have been out of the office until now and unable to give you feedback as well as upload a logo file. Thank you to all that have submitted and I hope this gives you a bit more breathing space due to my delayed responses. Cheers Jill

Target Market(s)

marketing the decision makers of sheet and plate metal work shops. They are 95% men, middle aged.

Industry/Entity Type

It Company

Requirements
Must have
• Must be A5 size utilizing all 4 pages. Photos that have been provided to be incorporated. If you don't want to use them all that is fine, I have provided probably more than needed.
Nice to have
• a small amount of metal graphic in there, but not over the top.
Should not have
• No old style fonts

```html
<!DOCTYPE html>
<html lang="en">
<head>
<meta charset="utf-8">
<title>Sheet Following System Brochure</title>
<link href="https://fonts.googleapis.com/css2?family=PT+Sans:wght@400;700&display=swap" rel="stylesheet">
<style>
  :root {
    --slate: #4a4a4c;
    --slate-dark: #3c3c3e;
    --machine-red: #e0301e;
    --brand-red: #d8262b;
    --text-light: #f2f2f2;
    --text-soft: #d9d9d9;
    --fold-line: #7a7a7c;
    --metal-light: #f4f4f4;
    --metal-mid: #b9bbbd;
    --metal-dark: #6d6f72;
  }
  * { margin: 0; padding: 0; box-sizing: border-box; }
  html, body { width: 1200px; height: 848px; overflow: hidden; background: var(--slate); }
  .spread {
    position: relative; width: 1200px; height: 848px;
    background: var(--slate);
    font-family: "PT Sans", sans-serif; color: var(--text-light);
  }
  .hero-photo {
    position: absolute; left: 0; top: 0; width: 1200px; height: 268px;
    background: linear-gradient(100deg, #8d8a86 0%, #6f6d6a 18%, #1d1d1f 32%, #2a2a2c 52%, #c8281a 60%, #e0301e 72%, #b42316 82%, #8a8783 92%, #9a9792 100%);
  }
  .hero-rule {
    position: absolute; left: 0; top: 268px; width: 1200px; height: 16px;
    background: linear-gradient(#cfcfcf, #9c9c9c 40%, var(--slate-dark));
    border-top: 1px solid #e8e8e8;
  }
  .fold { position: absolute; left: 589px; top: 0; width: 1px; height: 848px; background: var(--fold-line); opacity: .7; }
  .spec-title {
    position: absolute; left: 124px; top: 318px;
    font-size: 27px; color: var(--brand-red); font-weight: 400;
  }
  .spec-list {
    position: absolute; left: 182px; top: 353px; list-style: none;
    font-size: 14px; line-height: 17px; color: var(--text-light);
  }
  .contact-title {
    position: absolute; left: 124px; top: 484px;
    font-size: 48px; font-weight: 400; letter-spacing: 1px;
  }
  .address {
    position: absolute; left: 185px; top: 538px;
    font-size: 15px; line-height: 18px; color: var(--text-soft); font-style: normal;
  }
  .contact-row {
    position: absolute; left: 152px; display: flex; align-items: center; gap: 10px;
    font-size: 15px; color: var(--text-soft);
  }
  .contact-row svg { width: 22px; height: 18px; flex: none; }
  .web { position: absolute; left: 186px; top: 744px; font-size: 15px; color: var(--text-soft); }
  .product-name {
    position: absolute; left: 746px; top: 294px;
    font-size: 42px; font-weight: 400; color: var(--text-light); white-space: nowrap;
  }
  .brand {
    position: absolute; left: 876px; top: 358px; display: flex; align-items: center; gap: 10px;
  }
  .brand-mark { width: 14px; height: 14px; background: var(--brand-red); }
  .brand-name { font-size: 24px; font-weight: 400; color: var(--text-light); }
  .brand-tag {
    font-size: 12px; line-height: 16px; letter-spacing: 1.3px; color: var(--text-soft);
    border-top: 1px solid var(--brand-red); padding-top: 1px; text-transform: uppercase;
  }
  .product-photo {
    position: absolute; left: 952px; top: 448px; width: 238px; height: 322px;
    background: linear-gradient(160deg, #9fa3a6 0%, #5d5f62 28%, #1c1c1e 50%, #c8281a 72%, #e0301e 100%);
    clip-path: polygon(0 26%, 100% 0, 100% 100%, 20% 100%, 20% 60%);
  }
  .metal-bar {
    position: absolute; left: 0; top: 782px; width: 1200px; height: 16px;
    background: linear-gradient(var(--metal-dark), var(--metal-light) 35%, var(--metal-mid) 60%, var(--metal-dark));
  }
</style>
</head>
<body>
<main class="spread">
  <div class="hero-photo" role="img" aria-label="Close-up photo of the red and black sheet following machine on a concrete workshop floor"></div>
  <div class="hero-rule"></div>
  <div class="fold"></div>

  <h2 class="spec-title">Specifications</h2>
  <ul class="spec-list">
    <li>* Angle range of rotation 0 - 70 degrees</li>
    <li>* Load capacity per unit 300Kg maximum per unit</li>
    <li>* Height and width adjustments included</li>
    <li>* Stroke up/down 100mm</li>
    <li>* Length 700mm x Width 310mm x Height 960mm</li>
    <li>* Power 240v 10amps</li>
  </ul>

  <h2 class="contact-title">Contant Us</h2>
  <address class="address">
    Southern Fabrication Equipment<br>
    Services Pty Ltd (SFES)<br>
    Unit 4, 12-18 Harbour Road,<br>
    Bayfield&nbsp; NSW 2290
  </address>

  <div class="contact-row" style="top:626px">
    <svg viewBox="0 0 22 18"><rect x="2" y="3" width="18" height="12" fill="none" stroke="#d8262b" stroke-width="2"/><path d="M2 3 L11 10 L20 3" fill="none" stroke="#d8262b" stroke-width="2"/></svg>
    <span>PO Box 512, Bayfield&nbsp; NSW&nbsp; 2290</span>
  </div>
  <div class="contact-row" style="top:660px">
    <svg viewBox="0 0 22 18"><path d="M3 5 Q11 0 19 5 L17 8 L14 7 L14 5 L8 5 L8 7 L5 8 Z" fill="#d8262b"/><rect x="5" y="9" width="12" height="7" rx="1" fill="#d8262b"/></svg>
    <span>(+61) 2 5550 1200</span>
  </div>
  <div class="contact-row" style="top:688px">
    <svg viewBox="0 0 22 18"><rect x="6" y="1" width="10" height="6" fill="none" stroke="#d8262b" stroke-width="1.5"/><rect x="3" y="7" width="16" height="8" rx="1" fill="#d8262b"/><rect x="6" y="12" width="10" height="5" fill="#fff"/></svg>
    <span>(+61) 2 5550 1255</span>
  </div>
  <div class="contact-row" style="top:722px">
    <svg viewBox="0 0 22 18"><circle cx="11" cy="9" r="7" fill="none" stroke="#d8262b" stroke-width="2"/><circle cx="11" cy="9" r="3" fill="none" stroke="#d8262b" stroke-width="2"/></svg>
    <span>info@sfesgroup.com</span>
  </div>
  <div class="web">www.sfesgroup.com</div>

  <h1 class="product-name">Sheet Following System</h1>
  <div class="brand">
    <span class="brand-mark"></span>
    <span class="brand-name">SFES</span>
    <span class="brand-tag">Southern Fabrication<br>Equipment Services</span>
  </div>

  <div class="product-photo" role="img" aria-label="Photo of the sheet following unit with red base, black arm and tilted steel support plate"></div>

  <div class="metal-bar"></div>
</main>
</body>
</html>
```